Business Card Design Project

We are not a new company, but renamed to "Vantorin Kitchens" last year. We specialize in modern high-end cabinetry imports. We would like to communicate a sense of quality and cutting edge technology. Ideally the design would incorporate our logo colors, silver, red and preferably a black, matte background. Though we are open to suggestions.
Logo is attached.
Edit: I have attached rough drafts of the previous cards, this way you will have all necessary content that needs to go on the cards.
Updates
Project Deadline Extended
Reason: We have received a lot of great designs, but due to the sheer number we couldn't respond to all. We will extend the deadline for another 7 days to finalize and provide feedback to designers.
Thank you for your hard work!
Industry/Entity Type
Business
Look and feel
Each slider illustrates characteristics of the customer's brand and the style your logo design should communicate.

```html
<!DOCTYPE html>
<html lang="en">
<head>
<meta charset="utf-8">
<title>Vantorin Kitchens – Business Cards</title>
<link href="https://fonts.googleapis.com/css2?family=Arimo:wght@400;700&display=swap" rel="stylesheet">
<style>
  :root {
    --stage: #e6e2dc;
    --label: #2a2118;
    --card-top: #2e2e2e;
    --card-bottom: #121212;
    --card-plain: #0b0b0b;
    --silver: #c4c6c9;
    --silver-light: #e2e3e5;
    --silver-dark: #8d8f92;
    --red: #ec1c24;
    --white: #ffffff;
    --ink: #111111;
    --muted: #d6d6d6;
  }
  * { box-sizing: border-box; margin: 0; padding: 0; }
  html, body { width: 1200px; height: 788px; overflow: hidden; }
  body {
    position: relative;
    background: var(--stage);
    font-family: "Arimo", Arial, sans-serif;
  }
  .side-label {
    position: absolute;
    width: 200px;
    text-align: center;
    font-size: 22px;
    color: var(--label);
  }
  .card {
    position: absolute;
    width: 525px;
    height: 300px;
    border-radius: 22px;
    overflow: hidden;
    background: linear-gradient(180deg, var(--card-top), var(--card-bottom));
    box-shadow: 0 6px 14px rgba(0,0,0,.35);
  }
  .card--plain { background: var(--card-plain); }
  .brand-name {
    position: absolute;
    left: 0; right: 0;
    text-align: center;
    font-weight: 700;
    text-transform: uppercase;
    letter-spacing: 1px;
    color: var(--silver);
  }
  .card .brand-name { top: 97px; font-size: 26px; }
  .card--back .brand-name { top: 158px; font-size: 31px; }
  .band { position: absolute; left: 0; top: 156px; width: 525px; height: 65px; }
  .person {
    position: absolute; left: 49px; top: 170px; color: var(--white);
  }
  .person__name { font-size: 17px; font-weight: 700; text-transform: uppercase; line-height: 20px; }
  .person__name--light { font-weight: 400; }
  .person__role { font-size: 14px; line-height: 18px; }
  .direct-lines {
    position: absolute; right: 48px; top: 171px;
    text-align: right; font-size: 13.5px; line-height: 22px; color: var(--ink);
  }
  .direct-lines b { font-weight: 700; }
  .office {
    position: absolute; left: 0; right: 0; top: 240px;
    text-align: center; font-size: 13.5px; line-height: 23px; color: var(--muted);
  }
  .office b { color: var(--white); }
  .texture {
    position: absolute;
    width: 290px; height: 150px;
  }
  .texture--top {
    left: 0; top: 0;
    background: radial-gradient(ellipse at 45% 30%, #4a4a4a 0%, #1e1e1e 45%, transparent 75%);
  }
  .texture--bottom {
    right: 0; bottom: 0;
    background: radial-gradient(ellipse at 55% 70%, #4a4a4a 0%, #1e1e1e 45%, transparent 75%);
  }
</style>
</head>
<body>

  <div class="side-label" style="left:207px; top:22px;">front</div>
  <div class="side-label" style="left:789px; top:22px;">front-1</div>
  <div class="side-label" style="left:214px; top:405px;">back</div>
  <div class="side-label" style="left:781px; top:405px;">Back - 1</div>

  <!-- Front: President -->
  <section class="card card--front" style="left:53px; top:70px;">
    <div class="brand-name">Vantorin Kitchens</div>
    <svg class="band" viewBox="0 0 525 65" aria-hidden="true">
      <defs>
        <linearGradient id="silverBandA" x1="0" y1="0" x2="1" y2="0">
          <stop offset="0" stop-color="#8d8f92"/>
          <stop offset=".45" stop-color="#c4c6c9"/>
          <stop offset="1" stop-color="#d9dadc"/>
        </linearGradient>
      </defs>
      <polygon points="0,0 240,0 180,65 0,65" fill="#ec1c24"/>
      <polygon points="250,0 525,0 525,65 190,65" fill="url(#silverBandA)"/>
    </svg>
    <div class="person">
      <div class="person__name">Marek Dolan</div>
      <div class="person__role">President</div>
    </div>
    <div class="direct-lines">
      <div><b>phone</b> : 555.210.0148</div>
      <div><b>cell</b> : 555.210.3362</div>
    </div>
    <div class="office">
      <div><b>fax</b> : 555.210.0190 &nbsp;|&nbsp; marek@vantorinkitchens.ca</div>
      <div>4120 - 88 Ave., Calgary, AB T2R 4K5</div>
    </div>
  </section>

  <!-- Front: Director -->
  <section class="card card--front" style="left:619px; top:70px;">
    <div class="brand-name">Vantorin Kitchens</div>
    <svg class="band" viewBox="0 0 525 65" aria-hidden="true">
      <defs>
        <linearGradient id="silverBandB" x1="0" y1="0" x2="1" y2="0">
          <stop offset="0" stop-color="#8d8f92"/>
          <stop offset=".45" stop-color="#c4c6c9"/>
          <stop offset="1" stop-color="#d9dadc"/>
        </linearGradient>
      </defs>
      <polygon points="0,0 240,0 180,65 0,65" fill="#ec1c24"/>
      <polygon points="250,0 525,0 525,65 190,65" fill="url(#silverBandB)"/>
    </svg>
    <div class="person">
      <div class="person__name person__name--light">Anton Dolan</div>
      <div class="person__role">Director</div>
    </div>
    <div class="direct-lines">
      <div><b>phone</b> : 555.210.0148</div>
      <div><b>cell</b> : 555.210.7741</div>
    </div>
    <div class="office">
      <div><b>fax</b> : 555.210.0190 &nbsp;|&nbsp; anton@vantorinkitchens.ca</div>
      <div>4120 - 88 Ave., Calgary, AB T2R 4K5</div>
    </div>
  </section>

  <!-- Back -->
  <section class="card card--back" style="left:55px; top:447px;">
    <div class="brand-name">Vantorin Kitchens</div>
  </section>

  <!-- Back alternative -->
  <section class="card card--back card--plain" style="left:624px; top:446px;">
    <div class="texture texture--top" role="img" aria-label="Perforated metal texture in the top corner"></div>
    <div class="texture texture--bottom" role="img" aria-label="Perforated metal texture in the bottom corner"></div>
    <div class="brand-name">Vantorin Kitchens</div>
  </section>

</body>
</html>
```